Copperleaf Roofing Business Card

This is my current business card. But I’d like to make some changes. Somewhere on the card I’d like to list some of the services we offer. Maybe on the back? But I’d still like to keep the red. White and black modern look.

-residential & commercial roofing
-Roof Repairs & Maintenance
-Storm Damage & Insurance Claims specialist
-Christmas Lights and permanent Christmas lights
Fencing. Windows. Gutters. Siding. Sheetrock, painting.

```html
<!DOCTYPE html>
<html lang="en">
<head>
<meta charset="utf-8">
<title>Copperleaf Roofing Co. – Business Card</title>
<link rel="stylesheet" href="https://fonts.googleapis.com/css2?family=Audiowide&family=Montserrat:wght@400;500;800&display=swap">
<style>
  :root {
    --red: #d92d27;
    --black: #060607;
    --white: #ffffff;
    --ink: #141414;
    --stage: #3b3b3d;
  }
  * { box-sizing: border-box; margin: 0; padding: 0; }
  html, body { width: 1200px; height: 1059px; overflow: hidden; }
  body {
    background: var(--stage);
    font-family: "Montserrat", sans-serif;
    position: relative;
  }
  .card {
    position: absolute;
    left: 255px;
    width: 690px;
    height: 392px;
    border-radius: 16px;
    overflow: hidden;
    box-shadow: 6px 8px 16px rgba(0,0,0,.45);
  }
  .card--front { top: 100px; background: var(--white); }
  .card--back { top: 537px; background: var(--black); }

  .brand {
    position: absolute;
    left: 0; right: 0;
    text-align: center;
    font-family: "Montserrat", sans-serif;
    font-weight: 800;
    color: var(--red);
    line-height: 1.1;
    text-transform: uppercase;
  }
  .brand__dot {
    display: block;
    margin: 0 auto;
    border-radius: 50%;
    background: var(--red);
  }
  .card--front .brand { top: 58px; }
  .card--front .brand__dot { width: 108px; height: 108px; margin-bottom: 20px; }
  .card--front .brand__name { font-size: 27px; letter-spacing: 1px; }
  .card--front .brand__sub { font-size: 17px; letter-spacing: 1px; }

  .card--back .brand { top: 71px; }
  .card--back .brand__dot { width: 130px; height: 130px; margin-bottom: 20px; }
  .card--back .brand__name { font-size: 31px; letter-spacing: 1px; }
  .card--back .brand__sub { font-size: 20px; letter-spacing: 1px; }

  .person {
    position: absolute;
    right: 368px;
    top: 278px;
    text-align: right;
  }
  .person__name {
    font-family: "Audiowide", sans-serif;
    font-size: 24px;
    line-height: 1;
    color: var(--ink);
    text-transform: uppercase;
    white-space: nowrap;
  }
  .person__name span { color: var(--red); }
  .person__role {
    margin-top: 8px;
    font-size: 15px;
    color: var(--red);
    letter-spacing: .5px;
  }
  .divider {
    position: absolute;
    left: 344px;
    top: 270px;
    width: 1.5px;
    height: 70px;
    background: var(--ink);
  }
  .contact {
    position: absolute;
    left: 374px;
    top: 267px;
    list-style: none;
  }
  .contact li {
    display: flex;
    align-items: center;
    height: 26px;
    font-size: 15.5px;
    color: var(--ink);
  }
  .contact li.phone { letter-spacing: 2.5px; }
  .contact svg { width: 13px; height: 13px; margin-right: 9px; fill: var(--red); flex: none; }

  .services {
    position: absolute;
    left: 28px;
    right: 28px;
    top: 306px;
    color: var(--white);
    font-size: 15.5px;
    line-height: 26px;
  }
  .services__row { display: flex; justify-content: space-between; white-space: nowrap; }
  .services__item::before {
    content: "";
    display: inline-block;
    width: 7px; height: 7px;
    border-radius: 50%;
    background: var(--red);
    margin-right: 8px;
    vertical-align: middle;
  }

  .band {
    position: absolute;
    left: 0; right: 0; bottom: 0;
    height: 16px;
    background: var(--red);
  }
  .band__hatch {
    position: absolute;
    top: 0;
    width: 122px;
    height: 16px;
    clip-path: polygon(10px 0, 100% 0, calc(100% - 10px) 100%, 0 100%);
  }
  .band__hatch--left { left: 82px; }
  .band__hatch--right { left: 486px; }
  .card--front .band__hatch {
    background: repeating-linear-gradient(60deg, var(--black) 0 3px, var(--white) 3px 6px);
  }
  .card--back .band__hatch {
    background: repeating-linear-gradient(60deg, var(--white) 0 3px, var(--black) 3px 6px);
  }
</style>
</head>
<body>
  <section class="card card--front">
    <div class="brand">
      <span class="brand__dot"></span>
      <div class="brand__name">Copperleaf</div>
      <div class="brand__sub">Roofing Co.</div>
    </div>

    <div class="person">
      <div class="person__name"><span>Dana</span> Whitlock</div>
      <div class="person__role">OWNER</div>
    </div>
    <div class="divider"></div>
    <ul class="contact">
      <li class="phone">
        <svg viewBox="0 0 16 16"><path d="M3.6 1.2l2.3 2.6-1.2 2a9 9 0 0 0 5.5 5.5l2-1.2 2.6 2.3-1.3 2.3C7.8 16.2-.2 8.2 1.3 2.5z"/></svg>
        555-014-2287
      </li>
      <li>
        <svg viewBox="0 0 16 16"><path d="M1 3h14v2L8 9 1 5z M1 7l7 4 7-4v6H1z"/></svg>
        Dana@copperleafroofing.co
      </li>
      <li>
        <svg viewBox="0 0 16 16"><path d="M8 1a7 7 0 1 0 0 14A7 7 0 0 0 8 1zm0 1.4c.8.8 1.5 2.2 1.8 4.1H6.2C6.5 4.6 7.2 3.2 8 2.4zM2.5 7.5h2.3c0 .8.1 1.3.2 2H2.7a5.6 5.6 0 0 1-.2-2zm.6-1A5.6 5.6 0 0 1 6 2.7c-.6 1-1 2.3-1.2 3.8zm2.9 3h4c-.3 2-1 3.3-2 4.1-1-.8-1.7-2.1-2-4.1zm4.2-2c0 .8 0 1.3-.1 2H6c-.1-.7-.1-1.2-.1-2zm1 3h1.7a5.6 5.6 0 0 1-3 3.3c.6-1 1-2 1.3-3.3zm.2-1c.1-.7.2-1.2.2-2h2.3c0 .7-.1 1.3-.3 2zm.2-3c-.2-1.5-.6-2.8-1.2-3.8a5.6 5.6 0 0 1 2.9 3.8z"/></svg>
        www.copperleafroofing.co
      </li>
    </ul>

    <div class="band">
      <span class="band__hatch band__hatch--left"></span>
      <span class="band__hatch band__hatch--right"></span>
    </div>
  </section>

  <section class="card card--back">
    <div class="brand">
      <span class="brand__dot"></span>
      <div class="brand__name">Copperleaf</div>
      <div class="brand__sub">Roofing Co.</div>
    </div>

    <div class="services">
      <div class="services__row">
        <span class="services__item">Residential &amp; commercial roofing</span>
        <span class="services__item">Storm Damage &amp; Insurance Claims specialist</span>
      </div>
      <div class="services__row">
        <span class="services__item">Roof Repairs &amp; Maintenance</span>
        <span class="services__item">Christmas Lights and permanent Christmas lights</span>
      </div>
    </div>

    <div class="band">
      <span class="band__hatch band__hatch--left"></span>
      <span class="band__hatch band__hatch--right"></span>
    </div>
  </section>
</body>
</html>
```